Letterhead Design Project

I need letterhead designed for my law firm. It would also be used for web based stuff as well.

Industry/Entity Type

Law Firm

```html
<!DOCTYPE html>
<html lang="en">
<head>
<meta charset="utf-8">
<title>Harlow &amp; Vance — Letterhead</title>
<link rel="stylesheet" href="https://fonts.googleapis.com/css2?family=PT+Sans:wght@400&display=swap">
<style>
  :root {
    --backdrop: #000000;
    --paper: #ffffff;
    --navy: #2e3192;
    --brand-box: #2b2a7a;
    --name-band: #1f3442;
    --plaque-dark: #141414;
    --plaque-light: #3a3a3a;
    --portrait-a: #5a5a5e;
    --portrait-b: #4a3a30;
    --ink: #2e3192;
    --name-ink: #ffffff;
  }
  * { margin: 0; padding: 0; box-sizing: border-box; }
  html, body {
    width: 1200px; height: 1000px; overflow: hidden;
    background: var(--backdrop);
    font-family: "PT Sans", Arial, sans-serif;
  }
  .letterhead {
    position: absolute; left: 275px; top: 20px;
    width: 685px; height: 960px;
    background: var(--paper);
  }
  .footer-wave {
    position: absolute; left: 0; top: 0;
    width: 685px; height: 960px;
  }
  .brand-block {
    position: absolute; left: 19px; top: 18px;
    width: 213px; height: 213px;
    background: var(--brand-box);
  }
  .brand-name {
    position: absolute; left: 2px; top: 2px;
    width: 209px; height: 36px;
    background: var(--name-band);
    color: var(--name-ink);
    font-size: 20px; line-height: 36px;
    text-align: center; letter-spacing: 0.5px;
  }
  .brand-plaque {
    position: absolute; left: 22px; top: 45px;
    width: 166px; height: 41px;
    background: linear-gradient(180deg, var(--plaque-light), var(--plaque-dark));
  }
  .portrait {
    position: absolute; top: 97px;
  }
  .portrait--left {
    left: 15px; width: 72px; height: 90px;
    background: linear-gradient(180deg, var(--portrait-a), #2c2c30);
  }
  .portrait--right {
    left: 130px; width: 75px; height: 95px;
    background: linear-gradient(180deg, var(--portrait-b), #2a201c);
  }
  .contact {
    position: absolute; left: 430px; top: 28px;
    color: var(--ink);
    font-size: 21px; line-height: 28px;
    list-style: none;
  }
  .contact li.gap { margin-top: 28px; }
</style>
</head>
<body>
  <main class="letterhead">
    <svg class="footer-wave" viewBox="0 0 685 960" aria-hidden="true">
      <path d="M0 896 Q245 915 485 860 Q680 810 688 650 L688 960 L0 960 Z"
            fill="var(--navy)" stroke="#000" stroke-width="1"/>
    </svg>

    <div class="brand-block">
      <div class="brand-name">HARLOW &amp; VANCE</div>
      <div class="brand-plaque" role="img" aria-label="Dark metallic plaque reading law firm"></div>
      <div class="portrait portrait--left" role="img" aria-label="Portrait photo of the first partner"></div>
      <div class="portrait portrait--right" role="img" aria-label="Portrait photo of the second partner"></div>
    </div>

    <ul class="contact">
      <li>P.O.BOX 51-3904</li>
      <li>Lakeview,IL 60713</li>
      <li class="gap">(555)204-7719</li>
      <li>Harlowvance@mailbox.com</li>
      <li class="gap">www.harlow&amp;vance.com</li>
    </ul>
  </main>
</body>
</html>
```